Investment company needing business card

We are wanting a business card which looks sharp and easy on the eye. We are thinking of having a business card with the logo embossed on it, to really make it stand out. We will only have a small amount of information of the business card, person's name, position, email address and phone number

Contact Information for Business Card

Danielle Frost
Executive Assistant
+64 21 473 5162
danielf@harwickpartners.co.nz

Requirements
Must have
• Embossed logo
Should not have
• Not to be busy

```html
<!DOCTYPE html>
<html lang="en">
<head>
<meta charset="utf-8">
<title>Harwick Partners — Business Card</title>
<link href="https://fonts.googleapis.com/css2?family=Hind:wght@300;400;600&display=swap" rel="stylesheet">
<style>
  :root {
    --bg: #1c1c1c;
    --paper: #f1f1f0;
    --green: #23b26a;
    --grey: #6b6b6b;
    --text: #5a5a5a;
    --rule: #8a8a8a;
    --back: #1f1f1f;
    --back-mark: #2e2e2e;
  }
  * { margin: 0; padding: 0; box-sizing: border-box; }
  html, body { width: 1200px; height: 896px; overflow: hidden; }
  body {
    background: var(--bg);
    font-family: "Hind", sans-serif;
    position: relative;
  }
  .card {
    position: absolute;
    left: 351px;
    width: 489px;
    height: 278px;
  }
  .card-front { top: 160px; background: var(--paper); overflow: hidden; }
  .card-back {
    top: 470px;
    background: linear-gradient(160deg, #242424 0%, var(--back) 60%, #262626 100%);
  }
  .brand {
    position: absolute;
    display: flex;
    align-items: center;
    gap: 8px;
    white-space: nowrap;
  }
  .brand-square { width: 32px; height: 32px; flex: none; }
  .brand-name {
    font-weight: 600;
    font-size: 17.5px;
    letter-spacing: 0.2px;
    line-height: 1;
    padding-top: 4px;
    white-space: nowrap;
  }
  .card-front .brand { left: 27px; top: 119px; }
  .card-front .brand-square { background: var(--grey); }
  .card-front .brand-name { color: var(--green); }
  .divider {
    position: absolute;
    left: 274px; top: 73px;
    width: 1px; height: 132px;
    background: var(--rule);
  }
  .contact {
    position: absolute;
    left: 295px; top: 71px;
    color: var(--text);
  }
  .contact-name {
    color: var(--green);
    font-weight: 600;
    font-size: 18.5px;
    line-height: 22px;
  }
  .contact-role { font-weight: 300; font-size: 11px; line-height: 14px; margin-top: 2px; }
  .contact-address { font-weight: 300; font-size: 11px; line-height: 17.5px; margin-top: 5px; }
  .contact-list { list-style: none; margin-top: 4px; }
  .contact-list li {
    display: flex; align-items: center; gap: 6px;
    font-weight: 300; font-size: 11px; line-height: 17.5px;
    white-space: nowrap;
  }
  .contact-list svg { width: 9px; height: 9px; flex: none; }
  .band { position: absolute; left: 0; bottom: 0; width: 100%; height: 6px; }
  .card-back .brand { left: 50%; top: 50%; transform: translate(-50%, -50%); }
  .card-back .brand-square { background: var(--back-mark); }
  .card-back .brand-name { color: var(--back-mark); }
</style>
</head>
<body>
  <section class="card card-front">
    <div class="brand">
      <span class="brand-square"></span>
      <span class="brand-name">HARWICK PARTNERS</span>
    </div>
    <div class="divider"></div>
    <div class="contact">
      <p class="contact-name">Danielle Frost</p>
      <p class="contact-role">Executive Assistant</p>
      <p class="contact-address">1842 Larkspur Avenue River<br>mead, CA 92317</p>
      <ul class="contact-list">
        <li>
          <svg viewBox="0 0 10 10"><path d="M2 0.5 L3.6 2.6 L2.7 3.6 Q3.8 5.9 6.3 7.2 L7.3 6.3 L9.5 7.9 L8.4 9.5 Q1.5 8 0.5 1.6 Z" fill="#23b26a"/></svg>
          +64 21 473 5162
        </li>
        <li>
          <svg viewBox="0 0 10 10"><rect x="0.6" y="1.8" width="8.8" height="6.4" fill="none" stroke="#23b26a"/><path d="M0.6 1.8 L5 5.6 L9.4 1.8" fill="none" stroke="#23b26a"/></svg>
          danielf@harwickpartners.co.nz
        </li>
        <li>
          <svg viewBox="0 0 10 10"><circle cx="5" cy="5" r="4.3" fill="none" stroke="#23b26a"/><ellipse cx="5" cy="5" rx="1.9" ry="4.3" fill="none" stroke="#23b26a" stroke-width="0.8"/><path d="M0.7 5 H9.3" stroke="#23b26a" stroke-width="0.8"/></svg>
          www.harwickpartners.co.nz
        </li>
      </ul>
    </div>
    <svg class="band" viewBox="0 0 489 6" preserveAspectRatio="none">
      <polygon points="0,0 278,0 273,6 0,6" fill="#23b26a"/>
      <polygon points="281,0 489,0 489,6 276,6" fill="#6b6b6b"/>
    </svg>
  </section>

  <section class="card card-back">
    <div class="brand">
      <span class="brand-square"></span>
      <span class="brand-name">HARWICK PARTNERS</span>
    </div>
  </section>
</body>
</html>
```